Food broker, trader, wholesaler, liquidator looking for a 5 pages website

Looking for a 5 pages website design. We are food brokers, traders, wholesaler and closeout buyer working with manufacturers, distributors, importers sell to retailers, food service operators and industrial (ingredients). We help market their products. We are a resource for those who need a solution in the distribution/selling/placement of food on the shelves, kitchens and pantries. Whether we open new accounts with new products or sell short dated inventory, we know where to go and get results.

Target Market(s)

Food manufacturers, food distributors, food brokers

Coding

Coded - Design and coding required

Number of Pages Required

4 page

Font styles to use
Serif

Requirements
Must have
• Food-food production-warehouse-Food packaging-people meeting-trucks-supermarket shelves-

```html
<!DOCTYPE html>
<html lang="en">
<head>
<meta charset="utf-8">
<title>Harbor Provisions</title>
<link href="https://fonts.googleapis.com/css2?family=Libre+Baskerville:wght@400;700&family=Montserrat:wght@500;600;700&family=Open+Sans:wght@400;600&display=swap" rel="stylesheet">
<style>
:root{
  --navy:#14145e;
  --navy-deep:#0f0f52;
  --indigo:#2b2b86;
  --footer:#1d2192;
  --label:#5a5fa8;
  --grey:#555;
  --nav-grey:#7a7a7a;
  --white:#fff;
}
*{margin:0;padding:0;box-sizing:border-box}
html,body{width:1200px;height:3412px;overflow:hidden;background:var(--white)}
body{position:relative;font-family:'Open Sans',sans-serif;color:var(--grey)}
.abs{position:absolute}

/* header */
.header{position:absolute;top:0;left:0;width:1200px;height:93px;background:var(--white)}
.brand{position:absolute;left:92px;top:16px;display:flex;align-items:center;gap:12px}
.brand-dot{width:60px;height:60px;border-radius:50%;background:var(--navy)}
.brand-name{font-family:'Libre Baskerville',serif;font-weight:700;font-size:20px;color:var(--navy);letter-spacing:.3px}
.nav a{position:absolute;top:41px;transform:translateX(-50%);font-family:'Montserrat',sans-serif;font-weight:600;font-size:13px;color:var(--nav-grey);text-decoration:none;letter-spacing:.3px}
.nav a.active{color:var(--navy)}
.nav-bar{position:absolute;left:526px;top:0;width:66px;height:3px;background:var(--navy)}

/* hero */
.hero{position:absolute;top:93px;left:0;width:1200px;height:598px;background:linear-gradient(160deg,#4a74d0 0%,#2a4aa6 40%,#1b2a78 70%,#c98f1c 100%)}
.hero-ring{position:absolute;left:104px;top:177px;width:428px;height:428px;border-radius:50%;border:5px solid rgba(255,255,255,.75)}
.hero-disc{position:absolute;left:116px;top:189px;width:404px;height:404px;border-radius:50%;background:rgba(22,22,100,.93);text-align:center;color:var(--white)}
.hero-disc .welcome{margin-top:113px;font-family:'Libre Baskerville',serif;font-size:24px}
.hero-disc h1{margin-top:4px;font-family:'Libre Baskerville',serif;font-weight:700;font-size:42px;line-height:48px}
.btn{display:inline-block;border:2px solid currentColor;border-radius:30px;font-family:'Montserrat',sans-serif;font-weight:600;font-size:15px;text-decoration:none;text-align:center}
.hero-disc .btn{margin-top:20px;width:174px;height:52px;line-height:48px;color:var(--white)}

/* section titles */
.title{position:absolute;left:0;width:1200px;text-align:center;font-family:'Libre Baskerville',serif;font-weight:700;font-size:29px;color:var(--navy)}
.title::after{content:"";display:block;width:56px;height:3px;background:var(--navy);margin:9px auto 0}

/* about */
.about-text{position:absolute;left:165px;width:870px;top:838px;text-align:center;font-size:18px;line-height:27px;color:var(--grey)}
.about-text p+p{margin-top:12px}
.about-btn{position:absolute;left:504px;top:1019px;width:190px;height:56px;line-height:52px;color:var(--navy);font-size:16px}

/* what we do */
.service{position:absolute;border-radius:50%;color:var(--white);text-align:center;display:flex;flex-direction:column;align-items:center}
.service h3{font-family:'Montserrat',sans-serif;font-weight:700;font-size:18.5px;letter-spacing:.3px}
.service p{font-size:13px;line-height:21px;margin-top:8px}
.s-left{left:88px;top:1254px;width:336px;height:336px;background:radial-gradient(circle at 50% 40%,#2a3aa0,#17237a)}
.s-mid-ring{left:408px;top:1236px;width:382px;height:382px;background:var(--white);box-shadow:0 6px 24px rgba(0,0,0,.12)}
.s-mid{left:416px;top:1247px;width:366px;height:366px;background:radial-gradient(circle at 50% 40%,#2a2e80,#131555)}
.s-right{left:780px;top:1254px;width:336px;height:336px;background:radial-gradient(circle at 50% 40%,#3b55c4,#2335a6)}

/* why */
.why-panel{position:absolute;left:0;top:2232px;width:593px;height:547px;background:var(--navy-deep);clip-path:polygon(0 0,593px 0,593px 547px,0 474px)}
.why-photo{position:absolute;left:593px;top:2232px;width:607px;height:547px;background:linear-gradient(135deg,#d8b483 0%,#6f97cf 45%,#9fb3d6 80%,#c9d2e6 100%);clip-path:polygon(0 0,607px 0,607px 470px,0 547px)}
.why-title{position:absolute;left:158px;top:2338px;font-family:'Libre Baskerville',serif;font-weight:700;font-size:29px;color:var(--white)}
.why-rule{position:absolute;left:160px;top:2379px;width:56px;height:3px;background:var(--white)}
.why-text{position:absolute;left:160px;top:2410px;width:375px;color:var(--white);font-size:15.5px;line-height:27px}
.why-text p+p{margin-top:11px}
.why-btn{position:absolute;left:159px;top:2583px;width:168px;height:51px;line-height:47px;color:var(--white);font-size:14.5px}

/* contact */
.contact-bg{position:absolute;left:0;top:2779px;width:1200px;height:449px;background:linear-gradient(180deg,#fff 0%,#eef0f6 45%,#e4e7f1 75%,#f4f5fa 100%)}
.contact-desc{position:absolute;left:260px;width:680px;top:2910px;text-align:center;color:var(--indigo);font-size:16px;line-height:27px}
.c-icon{position:absolute;width:74px;height:74px;border-radius:50%;background:var(--footer);display:flex;align-items:center;justify-content:center}
.c-label{position:absolute;font-size:15px;color:var(--indigo)}
.c-value{position:absolute;font-size:21px;font-weight:600;color:var(--navy);white-space:nowrap}
.c-addr{position:absolute;font-size:17px;font-weight:600;color:var(--navy);line-height:27px}

/* footer */
.footer{position:absolute;left:0;top:3228px;width:1200px;height:184px;background:var(--footer);color:var(--white)}
.social{position:absolute;top:34px;width:35px;height:35px;border-radius:50%;border:2px solid var(--white)}
.foot-nav a{position:absolute;top:90px;transform:translateX(-50%);font-family:'Montserrat',sans-serif;font-weight:700;font-size:13.5px;color:var(--white);text-decoration:none}
.copyright{position:absolute;top:122px;left:0;width:1200px;text-align:center;font-size:12px}
</style>
</head>
<body>

<header class="header">
  <div class="brand"><span class="brand-dot"></span><span class="brand-name">HARBOR PROVISIONS</span></div>
  <span class="nav-bar"></span>
  <nav class="nav">
    <a class="active" href="#" style="left:560px">HOME</a>
    <a href="#" style="left:665px">ABOUT US</a>
    <a href="#" style="left:797px">WHAT WE DO</a>
    <a href="#" style="left:926px">CONTACT</a>
    <a href="#" style="left:1053px">GIVING BACK</a>
  </nav>
</header>

<section class="hero" role="img" aria-label="Beverage bottling line with orange juice bottles on a conveyor in a factory">
  <div class="hero-ring"></div>
  <div class="hero-disc">
    <div class="welcome">WELCOME TO</div>
    <h1>HARBOR<br>PROVISIONS</h1>
    <a class="btn" href="#">LEARN MORE</a>
  </div>
</section>

<h2 class="title" style="top:762px">ABOUT HARBOR PROVISIONS</h2>
<div class="about-text">
  <p>Harbor Provisions works with food manufacturers, brand owners, distributors and wholesalers market their products. Retail, Food Service and Industrial ingredients.</p>
  <p>Founded in 2008, Harbor Provisions started with the distribution of gluten free products understanding the need to provide access to unique flavors and products for the celiac consumers. From this, we expanded into deli, dairy, groceries, frozen and beverages.</p>
</div>
<a class="btn about-btn" href="#">LEARN MORE</a>

<h2 class="title" style="top:1165px">WHAT WE DO</h2>

<div class="service s-left" role="img" aria-label="Market data charts on a blue background">
  <svg style="margin-top:94px" width="68" height="60" viewBox="0 0 68 60" fill="none" stroke="#fff" stroke-width="2.5"><rect x="2" y="2" width="64" height="42" rx="3"/><path d="M10 34l12-14 9 9 10-15 8 10 9-12"/><path d="M34 44v9M20 57h28"/></svg>
  <h3 style="margin-top:14px">SALES &amp; MARKETING</h3>
  <p>we connect food buyers and sellers<br>through a dedicated approach.</p>
</div>

<div class="service s-mid-ring"></div>
<div class="service s-mid" role="img" aria-label="Cargo port with shipping containers at dusk">
  <svg style="margin-top:94px" width="80" height="80" viewBox="0 0 80 80" fill="none" stroke="#fff" stroke-width="2.5"><path d="M40 28l12 6v14l-12 6-12-6V34z"/><path d="M28 34l12 6 12-6M40 40v14"/><circle cx="40" cy="7" r="5"/><circle cx="8" cy="24" r="5"/><circle cx="72" cy="24" r="5"/><circle cx="8" cy="56" r="5"/><circle cx="72" cy="56" r="5"/><circle cx="40" cy="73" r="5"/><path d="M40 12v16M13 26l15 8M67 26l-15 8M13 54l15-6M67 54l-15-6M40 54v14"/></svg>
  <h3 style="margin-top:14px">TRADING</h3>
  <p>we purchase goods anywhere and ship<br>them Nationwide and Export.</p>
</div>

<div class="service s-right" role="img" aria-label="Worker checking stock in a storeroom">
  <svg style="margin-top:90px" width="64" height="64" viewBox="0 0 64 64" fill="none" stroke="#fff" stroke-width="2.5"><rect x="4" y="8" width="44" height="54" rx="2"/><rect x="16" y="3" width="20" height="9"/><path d="M11 24l3 3 5-6M24 24h16M11 36l3 3 5-6M24 36h16M11 48l3 3 5-6M24 48h12"/><path d="M44 30l14 14-6 6-14-14z"/><path d="M52 4v10M60 4v10"/></svg>
  <h3 style="margin-top:12px">EXCESS INVENTORY</h3>
  <p>We buy closeouts and excess inventory<br>for prisons, outlet stores and<br>discounters.</p>
</div>

<h2 class="title" style="top:1711px">OUR CYCLE</h2>

<svg class="abs" style="left:0;top:1780px" width="1200" height="420" viewBox="0 1344 906 317" font-family="Montserrat, sans-serif" font-weight="700" font-size="9" fill="none">
  <circle cx="448" cy="1467" r="128" stroke="#c9cbe3" stroke-width="1.5" stroke-dasharray="6 5"/>
  <circle cx="448" cy="1467" r="96" fill="#fff" stroke="#f0f0f4" stroke-width="4"/>
  <circle cx="448" cy="1467" r="70" fill="#14145e"/>
  <text x="448" y="1464" text-anchor="middle" fill="#fff" font-family="Libre Baskerville, serif" font-size="11">HARBOR</text>
  <text x="448" y="1479" text-anchor="middle" fill="#fff" font-family="Libre Baskerville, serif" font-size="11">PROVISIONS</text>
  <g stroke="#1b1f7a" stroke-width="1.4" fill="#fff">
    <circle cx="354" cy="1380" r="6"/><circle cx="322" cy="1461" r="6"/><circle cx="348" cy="1551" r="6"/>
    <circle cx="449" cy="1594" r="6"/><circle cx="543" cy="1551" r="6"/><circle cx="570" cy="1461" r="6"/><circle cx="537" cy="1379" r="6"/>
  </g>
  <g fill="#5a5fa8">
    <text x="291" y="1381" text-anchor="end">FOOD</text>
    <text x="255" y="1464" text-anchor="end">FOOD</text>
    <text x="255" y="1476" text-anchor="end">PRODUCTION</text>
    <text x="291" y="1580" text-anchor="end">WAREHOUSE</text>
    <text x="451" y="1654" text-anchor="middle">FOOD PACKAGING</text>
    <text x="599" y="1576">PEOPLE MEETING</text>
    <text x="628" y="1471">TRUCKS</text>
    <text x="595" y="1381">SUPERMARKET</text>
    <text x="595" y="1393">SHELVES</text>
  </g>
  <g stroke="#1b1f7a" stroke-width="1.6" stroke-linejoin="round">
    <path d="M303 1368h30v5h-30zM305 1373l2 16h22l2-16M311 1363h14v5M318 1373v16"/>
    <path d="M271 1466l3-10h3l3 10v16h-9zM282 1466l3-10h3l3 10v16h-9zM293 1466l3-10h3l3 10v16h-9zM271 1472h31"/>
    <path d="M302 1579v-20l16-9 16 9v20zM309 1579v-14h18v14M313 1571h10v8h-10z"/>
    <path d="M434 1616l15-7 15 7v16l-15 7-15-7zM434 1616l15 7 15-7M449 1623v16M453 1630c3-4 7-4 8-1"/>
    <path d="M558 1578v-6c0-5 3-8 7-8s7 3 7 8v6zM572 1578v-6c0-5 3-8 7-8s7 3 7 8v6z"/><circle cx="565" cy="1557" r="4"/><circle cx="579" cy="1557" r="4"/><circle cx="572" cy="1549" r="4"/>
    <path d="M600 1472v-18h20v18zM600 1460h-8l-5 6v6h13"/><circle cx="592" cy="1474" r="3" fill="#fff"/><circle cx="613" cy="1474" r="3" fill="#fff"/>
    <path d="M558 1366h26v26h-26zM558 1374h26M558 1383h26M562 1366v-4M580 1366v-4M563 1378h4M570 1378h4M577 1378h4M563 1387h4M570 1387h4"/>
  </g>
</svg>

<div class="why-panel"></div>
<div class="why-photo" role="img" aria-label="Large warehouse with tall blue racks stacked with cardboard boxes"></div>
<h2 class="why-title">WHY WE ARE</h2>
<span class="why-rule"></span>
<div class="why-text">
  <p>Augiat in pede Fusce tellus Sed metus augue convallis et vehicula ut pulvinar eu ante Integer</p>
  <p>Auscipit leo massa sodales velit et scelerisque mi tortor at ipsum Proin orci odio commodo ac gravida non tristique vel te Curabitur iaculis tempu</p>
</div>
<a class="btn why-btn" href="#">LEARN MORE</a>

<div class="contact-bg" role="img" aria-label="Faded view of a distribution warehouse interior"></div>
<h2 class="title" style="top:2855px">CONTACT US</h2>
<p class="contact-desc">Augiat in pede Fusce tellus Sed metus augue convallis et vehicula ut pulvinar eu ante Integer orci tellus tristique vitae</p>

<div class="c-icon" style="left:205px;top:3033px"><svg width="34" height="34" viewBox="0 0 24 24" fill="#fff"><path d="M6.6 10.8a15 15 0 0 0 6.6 6.6l2.2-2.2c.3-.3.7-.4 1-.2 1.1.4 2.3.6 3.6.6.6 0 1 .4 1 1V20c0 .6-.4 1-1 1A17 17 0 0 1 3 4c0-.6.4-1 1-1h3.5c.6 0 1 .4 1 1 0 1.3.2 2.5.6 3.6.1.3 0 .7-.2 1z"/></svg></div>
<div class="c-label" style="left:294px;top:3040px">PHONE NUMBER</div>
<div class="c-value" style="left:294px;top:3060px">(555) 214 7730</div>

<div class="c-icon" style="left:494px;top:3033px"><svg width="34" height="26" viewBox="0 0 34 26" fill="#fff"><path d="M0 2l17 12L34 2V0H0z"/><path d="M0 6v20h34V6L17 18z"/></svg></div>
<div class="c-label" style="left:583px;top:3040px">EMAIL US</div>
<div class="c-value" style="left:583px;top:3064px;font-size:17px">info@harborprov.com</div>

<div class="c-icon" style="left:808px;top:3025px"><svg width="28" height="38" viewBox="0 0 24 32" fill="#fff"><path d="M12 0C5.4 0 0 5.2 0 11.7 0 20 12 32 12 32s12-12 12-20.3C24 5.2 18.6 0 12 0zm0 16a4.5 4.5 0 1 1 0-9 4.5 4.5 0 0 1 0 9z"/></svg></div>
<div class="c-label" style="left:897px;top:3032px">ADDRESS</div>
<div class="c-addr" style="left:897px;top:3055px">48 Pier Lane, Suite 5<br>Bayview TX 77001</div>

<footer class="footer">
  <span class="social" style="left:514px"></span>
  <span class="social" style="left:554px"></span>
  <span class="social" style="left:595px"></span>
  <span class="social" style="left:635px"></span>
  <nav class="foot-nav">
    <a href="#" style="left:331px">HOME</a>
    <a href="#" style="left:435px">ABOUT US</a>
    <a href="#" style="left:567px">WHAT WE DO</a>
    <a href="#" style="left:697px">CONTACT</a>
    <a href="#" style="left:824px">GIVING BACK</a>
  </nav>
  <p class="copyright">© 2020 Harbor Provisions | All Rights Reserved | Disclaimer</p>
</footer>

</body>
</html>
```